Upscale business cards needed for Board of Directors

We need professional business cards created for members of our family business Board of Directors. We would like these relatively simple and straightforward, but also with a unique element to set them apart. Probably stick with neutral and simple colors - white, grey etc. We need space for the traditional elements, including name, title, address, email/phone number. And we will be creating several from this template so it needs to be template that is easy to switch information in and out of.
Business
See description

```html
<!DOCTYPE html>
<html lang="en">
<head>
<meta charset="utf-8">
<title>Harborline Holdings – Business Cards</title>
<link href="https://fonts.googleapis.com/css2?family=Lato:wght@400;900&display=swap" rel="stylesheet">
<style>
  :root {
    --stage: #3a3a3a;
    --card: #ffffff;
    --ink: #111111;
    --gold: #b3a27a;
    --band: #0c0c0c;
  }
  * { margin: 0; padding: 0; box-sizing: border-box; }
  html, body { width: 1200px; height: 900px; overflow: hidden; }
  body {
    background: var(--stage);
    font-family: "Lato", sans-serif;
    position: relative;
  }
  .card {
    position: absolute;
    left: 320px;
    width: 560px;
    height: 320px;
    background: var(--card);
    box-shadow: 0 10px 30px rgba(0,0,0,0.45);
    overflow: hidden;
  }
  .card--back { top: 90px; }
  .card--front { top: 470px; }

  .wordmark {
    font-weight: 900;
    color: var(--ink);
    text-transform: uppercase;
    line-height: 1.05;
  }
  .card--back .wordmark {
    position: absolute;
    top: 96px;
    left: 0; right: 0;
    text-align: center;
    font-size: 40px;
    letter-spacing: 1px;
  }
  .wordmark .sub { display: block; font-size: 0.5em; letter-spacing: 0.5em; }
  .card--back .site {
    position: absolute;
    bottom: 52px; left: 0; right: 0;
    text-align: center;
    font-size: 14px;
    letter-spacing: 2px;
    color: var(--ink);
  }

  .card--front .wordmark {
    position: absolute;
    top: 32px; left: 40px;
    font-size: 34px;
    letter-spacing: 1px;
  }
  .contact {
    position: absolute;
    top: 126px; left: 40px;
    font-size: 13px;
    color: var(--ink);
    line-height: 1.4;
    list-style: none;
  }
  .contact li { display: flex; align-items: center; gap: 8px; }
  .contact .address { padding-left: 20px; margin-bottom: 2px; }
  .contact svg { width: 12px; height: 12px; fill: var(--gold); flex: none; }

  .person {
    position: absolute;
    right: 40px; top: 168px;
    text-align: right;
  }
  .person .name { font-size: 24px; color: var(--gold); font-weight: 400; }
  .person .title { font-size: 15px; color: var(--ink); margin-top: 2px; }

  .footer-band { position: absolute; left: 0; bottom: 0; width: 560px; height: 60px; }
  .footer-band .site {
    position: absolute;
    right: 36px; bottom: 12px;
    font-size: 17px;
    letter-spacing: 1.5px;
    color: #ffffff;
  }
</style>
</head>
<body>

  <section class="card card--back" aria-label="Card back">
    <div class="wordmark">Harborline<span class="sub">Holdings</span></div>
    <div class="site">www.harborline.com</div>
  </section>

  <section class="card card--front" aria-label="Card front">
    <div class="wordmark">Harborline<span class="sub">Holdings</span></div>

    <ul class="contact">
      <li class="address">1450 Cedar Lane<br>Marlow TX 78100</li>
      <li><svg viewBox="0 0 12 12"><path d="M2.5 0.5l2 2.5-1.2 1.4c.7 1.6 1.7 2.6 3.3 3.3L8 6.5l2.5 2-1 2.5C5 10.5 1.5 7 1 2.5z"/></svg>555 014 2200</li>
      <li><svg viewBox="0 0 12 12"><rect x="3" y="0.5" width="6" height="3"/><rect x="0.5" y="4" width="11" height="5" rx="1"/><rect x="3" y="8" width="6" height="3.5"/></svg>555 014 2201</li>
      <li><svg viewBox="0 0 12 12"><path d="M0.5 2h11v8h-11z M0.5 2l5.5 4.5 5.5-4.5"/></svg>info@harborline.com</li>
    </ul>

    <div class="person">
      <div class="name">Daniel Whitford</div>
      <div class="title">Director</div>
    </div>

    <div class="footer-band">
      <svg width="560" height="60" viewBox="0 0 560 60">
        <line x1="0" y1="22" x2="238" y2="22" stroke="var(--gold)" stroke-width="4"/>
        <path d="M0 48 H246 C262 48 262 18 284 18 H560 V60 H0 Z" fill="var(--band)"/>
      </svg>
      <div class="site">www.harborline.com</div>
    </div>
  </section>

</body>
</html>
```